Stationary design for boutique production house

We need a stationary design for our production house, 'Lorno Productions' based in Singapore. We produce microfilms as well as podcasts, talkshows and events. Our logo is a stylized icon of our director, who is also the executive producer and host of our programs, Lorno. Our main company colors are Red, Black and white. We would like a clean, minimalist design incorporating our existing company logo that conveys a sense of urbanism and elegance.

Logo and font files are attached. f

Target Market(s)

We focus on lifestyle media rather than entertainment.

Industry/Entity Type

Boutique

Font styles to use
Serif
Sans Serif

Colors
ec1f27
ffffff
000000

Requirements
Must have
• Our company logo and at least one of our company colors.
Nice to have
• Our address and contact information.
Should not have
• Changes made to the company logo (using only certain parts of it is fine though)

```html
<!DOCTYPE html>
<html lang="en">
<head>
<meta charset="utf-8">
<title>Lorno Productions — Business Card</title>
<link rel="stylesheet" href="https://fonts.googleapis.com/css2?family=Jost:wght@400&display=swap">
<style>
  :root {
    --red: #d0191f;
    --black: #1b1b1b;
    --white: #ffffff;
    --paper: #f7f7f7;
    --backdrop: #505050;
    --text: #333333;
  }
  * { margin: 0; padding: 0; box-sizing: border-box; }
  html, body { width: 1200px; height: 750px; overflow: hidden; }
  body {
    background: var(--backdrop);
    font-family: "Jost", "Futura", sans-serif;
    font-weight: 400;
    position: relative;
  }
  .card {
    position: absolute;
    top: 228px;
    width: 462px;
    height: 263px;
  }
  .card--front { left: 124px; background: var(--paper); }
  .card--back { left: 595px; background: var(--red); }

  .contact { position: absolute; left: 44px; top: 44px; color: var(--text); }
  .contact__name { color: var(--red); font-size: 19px; letter-spacing: 0.2px; line-height: 1.1; }
  .contact__role { color: var(--black); font-size: 14px; margin-top: 2px; }
  .contact__address { font-size: 12px; line-height: 14px; margin-top: 10px; }
  .contact__list { list-style: none; margin-top: 10px; font-size: 12px; }
  .contact__list li { display: flex; align-items: center; height: 17.6px; }
  .contact__list svg { width: 13px; height: 13px; margin-right: 7px; flex: none; }

  .brand {
    position: absolute; left: 280px; top: 72px; width: 140px;
    display: flex; flex-direction: column; align-items: center;
  }
  .brand__dot { width: 12px; height: 12px; border-radius: 50%; background: var(--red); margin-bottom: 14px; }
  .brand__name { color: var(--black); font-size: 18px; line-height: 1.15; text-align: center; letter-spacing: 0.5px; }

  .back__brand {
    position: absolute; left: 0; right: 0; top: 88px;
    display: flex; flex-direction: column; align-items: center;
  }
  .back__dot { width: 12px; height: 12px; border-radius: 50%; background: var(--white); margin-bottom: 12px; }
  .back__name { color: var(--white); font-size: 30px; letter-spacing: 1px; }
  .back__web {
    position: absolute; left: 0; right: 0; top: 222px;
    text-align: center; color: var(--white); font-size: 11px; letter-spacing: 6px;
  }
</style>
</head>
<body>
  <section class="card card--front">
    <div class="contact">
      <h1 class="contact__name">MARA QUILL</h1>
      <p class="contact__role">CEO/FOUNDER</p>
      <p class="contact__address">42 Keong Saik Road<br>Singapore 089150</p>
      <ul class="contact__list">
        <li><svg viewBox="0 0 14 14"><circle cx="7" cy="7" r="7" fill="var(--red)"/><path d="M4.5 3.5l1.5 1.5-0.8 1c0.5 1 1.3 1.8 2.3 2.3l1-0.8 1.5 1.5-1 1c-2.6-0.5-4.5-2.4-5-5z" fill="#fff"/></svg>6218 4570</li>
        <li><svg viewBox="0 0 14 14"><circle cx="7" cy="7" r="7" fill="var(--red)"/><rect x="5" y="3.5" width="4" height="7" rx="0.8" fill="#fff"/></svg>9364 2811</li>
        <li><svg viewBox="0 0 14 14"><circle cx="7" cy="7" r="7" fill="var(--red)"/><rect x="3.5" y="5.5" width="7" height="4" rx="0.6" fill="#fff"/><rect x="5" y="3.5" width="4" height="2" fill="#fff"/></svg>6218 4571</li>
        <li><svg viewBox="0 0 14 14"><circle cx="7" cy="7" r="7" fill="var(--red)"/><rect x="3.5" y="4.5" width="7" height="5" fill="#fff"/><path d="M3.5 4.5l3.5 2.8 3.5-2.8" stroke="var(--red)" stroke-width="0.8" fill="none"/></svg>mara@lornoprod.com</li>
        <li><svg viewBox="0 0 14 14"><circle cx="7" cy="7" r="7" fill="var(--red)"/><circle cx="7" cy="7" r="3.3" fill="none" stroke="#fff" stroke-width="1.2"/></svg>www.lornoprod.com</li>
      </ul>
    </div>
    <div class="brand">
      <span class="brand__dot"></span>
      <span class="brand__name">LORNO<br>PRODUCTIONS</span>
    </div>
  </section>

  <section class="card card--back">
    <div class="back__brand">
      <span class="back__dot"></span>
      <span class="back__name">LORNO</span>
    </div>
    <p class="back__web">www.lornoprod.com</p>
  </section>
</body>
</html>
```